R7M Horizon Business Card Design

We need a business card created for our New Business "R7M Horizon"<br/><br/>The business card design is up to you however the following information must be on the business card:<br/><br/>Front of the business card -<br/>Email :darrenp@r7mhorizon.nz<br/>Mobile: +64 (0) 22 4870 619<br/>Website: www.r7mhorizon.nz<br/>Card Owner Name: Darren Paltrow<br/>Company Title: Business Development Manager<br/>Slogan: "The BEST of both worlds". <br/>Logo On the front attached to the design brief<br/><br/>On the back: <br/>Space on the back for 4 more versions of the logo across the bottom of the card indicating different subsidiary brands - R7M Coffee, R7M Arts, R7M ?? (The card will be used for all of these brands - We Will add the extra subsidiary logos to the design once the design is finished (We are a graphics design team). <br/><br/>Other than that we want a premium feeling logo that remains universally usable depending on the business entity that we are using the card for. The use of bright bold colours would be great but we still want the card to feel premium.
Target Market(s)
Gift Design and Manufacturing Companies
Contact Information for Business Card
Front of the business card -
Email :darrenp@r7mhorizon.nz
Mobile: +64 (0) 22 4870 619
Website: www.r7mhorizon.nz
Card Owner Name: Darren Paltrow
Company Title: Business Development Manager
Slogan: "The BEST of both worlds".
Logo On the front attached to the design brief

```html
<!DOCTYPE html>
<html lang="en">
<head>
<meta charset="utf-8">
<title>R7M Horizon Business Card</title>
<link href="https://fonts.googleapis.com/css2?family=Titillium+Web:wght@400;600;700&display=swap" rel="stylesheet">
<style>
  :root {
    --page: #e9e6e1;
    --card-white: #ffffff;
    --brand-blue: #2f3a8f;
    --stripe-blue: #3a4aa6;
    --ink: #222326;
    --back-dark: #1d2126;
    --back-dark-2: #262b31;
    --back-mark: #3a3f46;
  }
  * { box-sizing: border-box; margin: 0; padding: 0; }
  html, body { width: 1200px; height: 859px; overflow: hidden; }
  body {
    background: var(--page);
    font-family: "Titillium Web", Arial, sans-serif;
    position: relative;
  }
  .card {
    position: absolute;
    top: 287px;
    width: 500px;
    height: 285px;
    border-radius: 10px;
    overflow: hidden;
    box-shadow: 0 6px 16px rgba(0,0,0,0.18);
  }
  .card-front { left: 60px; background: var(--card-white); }
  .card-back {
    left: 640px;
    background: linear-gradient(135deg, var(--back-dark-2), var(--back-dark));
  }
  .card svg.decor { position: absolute; inset: 0; }

  .brand-name {
    position: absolute;
    left: 24px;
    top: 38px;
    color: var(--brand-blue);
    font-weight: 700;
    font-size: 34px;
    line-height: 1;
    white-space: nowrap;
  }
  .accent-bar {
    position: absolute;
    left: 0; top: 134px;
    width: 6px; height: 30px;
    background: var(--brand-blue);
  }
  .holder {
    position: absolute;
    left: 24px; top: 132px;
  }
  .holder-name {
    color: var(--brand-blue);
    font-weight: 700;
    font-size: 19px;
    line-height: 1.1;
    letter-spacing: 0.2px;
    white-space: nowrap;
  }
  .holder-title {
    color: var(--ink);
    font-size: 13px;
    line-height: 1.2;
    letter-spacing: -0.2px;
    white-space: nowrap;
  }
  .contacts {
    position: absolute;
    left: 24px; top: 183px;
    list-style: none;
  }
  .contacts li {
    display: flex;
    align-items: center;
    gap: 6px;
    font-size: 13px;
    line-height: 17px;
    color: var(--ink);
    white-space: nowrap;
  }
  .contacts svg { width: 12px; height: 12px; flex: none; }
  .slogan {
    position: absolute;
    left: 24px; top: 249px;
    color: var(--brand-blue);
    font-size: 13.5px;
    white-space: nowrap;
  }
  .back-name {
    position: absolute;
    left: 0; right: 0; top: 122px;
    text-align: center;
    color: var(--back-mark);
    font-weight: 700;
    font-size: 34px;
    line-height: 1;
    white-space: nowrap;
  }
</style>
</head>
<body>
  <section class="card card-front" aria-label="Card front">
    <svg class="decor" width="500" height="285" viewBox="0 0 500 285" aria-hidden="true">
      <polygon points="286,285 500,70 500,146 362,285" fill="var(--stripe-blue)"/>
      <polygon points="437,285 500,222 500,285" fill="var(--stripe-blue)"/>
    </svg>
    <p class="brand-name">R7M Horizon</p>
    <div class="accent-bar"></div>
    <div class="holder">
      <p class="holder-name">DARREN PALTROW</p>
      <p class="holder-title">Business Development Manager</p>
    </div>
    <ul class="contacts">
      <li>
        <svg viewBox="0 0 12 12" aria-hidden="true"><circle cx="6" cy="6" r="5" fill="none" stroke="var(--ink)" stroke-width="1"/><path d="M4 3.5 L5 3.5 L5.5 5 L4.8 5.5 Q5.5 7 6.8 7.4 L7.3 6.7 L8.6 7.2 L8.5 8.2 Q5 8.5 3.7 4.3 Z" fill="var(--ink)"/></svg>
        +64 (0) 22 4870 619
      </li>
      <li>
        <svg viewBox="0 0 12 12" aria-hidden="true"><rect x="1" y="2.5" width="10" height="7" fill="none" stroke="var(--ink)" stroke-width="1"/><path d="M1 2.5 L6 6.5 L11 2.5" fill="none" stroke="var(--ink)" stroke-width="1"/></svg>
        darrenp@r7mhorizon.nz
      </li>
      <li>
        <svg viewBox="0 0 12 12" aria-hidden="true"><circle cx="6" cy="6" r="5" fill="none" stroke="var(--ink)" stroke-width="1"/><ellipse cx="6" cy="6" rx="2.2" ry="5" fill="none" stroke="var(--ink)" stroke-width="0.9"/><path d="M1 6 H11 M2 3.5 H10 M2 8.5 H10" stroke="var(--ink)" stroke-width="0.8"/></svg>
        www.r7mhorizon.nz
      </li>
    </ul>
    <p class="slogan">The BEST of both worlds</p>
  </section>

  <section class="card card-back" aria-label="Card back">
    <svg class="decor" width="500" height="285" viewBox="0 0 500 285" aria-hidden="true">
      <polygon points="67,0 143,0 0,143 0,67" fill="var(--stripe-blue)"/>
    </svg>
    <p class="back-name">R7M Horizon</p>
  </section>
</body>
</html>
```